Business Card Design Project

Business Card
We are rebranding with a new logo
Industry/Entity Type
Business
Contact Information for Business Card
Dennis Morvale +61 487215963 dennis@quorv.com.au P.O. Box 872 Fernlow QLD 4309
Requirements
Must have
- Logo

```html
<!DOCTYPE html>
<html lang="en">
<head>
<meta charset="utf-8">
<title>Quorv International – Business Card</title>
<link href="https://fonts.googleapis.com/css2?family=Exo+2:wght@400;500&display=swap" rel="stylesheet">
<style>
  :root {
    --page-bg: #e6e6e6;
    --card-bg: #ffffff;
    --brand-blue: #1d5f86;
    --label-blue: #1b5a7e;
    --text-grey: #9a9a9a;
    --accent-orange: #f07a12;
  }
  html, body {
    margin: 0;
    width: 1200px;
    height: 1000px;
    overflow: hidden;
    background: var(--page-bg);
    font-family: "Exo 2", sans-serif;
  }
  .card {
    position: absolute;
    left: 68px;
    top: 197px;
    width: 1064px;
    height: 606px;
    background: var(--card-bg);
    box-shadow: 0 6px 18px rgba(0,0,0,0.12);
  }
  .brand {
    position: absolute;
    left: 140px;
    top: 150px;
    display: flex;
    align-items: center;
    gap: 14px;
  }
  .brand-dot {
    width: 26px;
    height: 26px;
    border-radius: 50%;
    background: var(--accent-orange);
  }
  .brand-name {
    font-size: 30px;
    font-weight: 500;
    color: var(--brand-blue);
    letter-spacing: 1px;
  }
  .contact {
    position: absolute;
    left: 564px;
    top: 150px;
    font-size: 23px;
    line-height: 34px;
    color: var(--text-grey);
    letter-spacing: 0.5px;
  }
  .contact .label {
    color: var(--label-blue);
    font-weight: 500;
  }
  .person {
    position: absolute;
    left: 140px;
    top: 449px;
    display: flex;
    align-items: stretch;
    gap: 32px;
  }
  .person-bar {
    width: 11px;
    background: var(--brand-blue);
  }
  .person-name {
    font-size: 27px;
    line-height: 32px;
    color: var(--text-grey);
    text-transform: uppercase;
    letter-spacing: 0.5px;
  }
  .address {
    position: absolute;
    left: 564px;
    top: 483px;
    font-size: 23px;
    color: var(--text-grey);
    letter-spacing: 0.5px;
  }
</style>
</head>
<body>
  <main class="card">
    <div class="brand">
      <span class="brand-dot"></span>
      <span class="brand-name">Quorv International</span>
    </div>
    <div class="contact">
      <div><span class="label">Cell:</span> +61 487215963</div>
      <div><span class="label">Mob:</span> dennis@quorv.com.au</div>
    </div>
    <div class="person">
      <span class="person-bar"></span>
      <div class="person-name">Dennis<br>Morvale</div>
    </div>
    <div class="address">P.O. Box 872 Fernlow QLD 4309</div>
  </main>
</body>
</html>
```